Onboarding Infographic/brochure

We are a small criminal defense firm looking to create some sort of infographic or brochure that we can onboard new clients with. We are currently sending it out via email but want something a bit cooler and fun to send to clients. The information is:

A Few Quick Rules

We are here to help each step of the way. While questions are never discouraged, this letter will answer some of the most common ones we get asked.

Communications

As a client, you should always be in the loop. While we will try to respond to questions as quickly as possible, sometimes we are unable to respond right away. Do not worry - we promise to get back to you soon. Some questions might take some time to research, and a correct answer is better than a quick one.

Appointments

One of the benefits of having an attorney is the ability to discuss your case outside of court, minus the stress and headaches. If you need an appointment, please contact the office.

Appointments must be scheduled in advance. We do not want you to make a special trip to the office only to learn that we are in court or otherwise unavailable.

Jail Visits

If your family member is currently in jail, we take that very seriously. We will visit your loved one and introduce ourselves. While the case is ongoing, we ask that a family member be designated a “contact” person so that messages can be relayed quickly. Never discuss the facts of the case over the phone with someone who is in jail. Jail calls are recorded and we have seen too many cases go south based on remarks made over recorded lines.

Police Reports and Discovery

We will do our best to provide you with copies of everything we receive on your case. Most information will be emailed, so please keep your email address up to date.

Changes in Contact Information

If you move or change numbers during the case, please let us know. It is difficult to help if we are unable to reach you, and helping you is why we are here.

Court Appearances

Cases do not get resolved as quickly as they do on television. Expect there to be several hearings in your case and it may be necessary for you to attend one or more of them. If a hearing is set, you will receive notice of the date and time of each hearing.

Billing and Collections

We understand that this investment was a huge decision for you. As we focus on providing the best representation, we will need for you to stay on schedule with any payment arrangements agreed to at the time of your initial consultation.

Again, thank you for your trust in us. We look forward to getting a fantastic outcome on your case.

Target Market(s)

Criminal defense clients and their families

Industry/Entity Type

Legal

Font styles to use
Serif

Requirements
Must have
• Must incorporate all of the rules we email out. Would like diagrams, images or pictures
Nice to have
• We attached a Welcome brochure. Not sure I want it to look super similar, hence the request for infographic.

```html
<!DOCTYPE html>
<html lang="en">
<head>
<meta charset="utf-8">
<title>Client Onboarding – A Few Quick Rules</title>
<link rel="stylesheet" href="https://fonts.googleapis.com/css2?family=Barlow:wght@400&family=Montserrat:wght@500&display=swap">
<style>
  :root {
    --page: #ffffff;
    --panel-light: #f1f1f1;
    --row-1: #aed0f0;
    --row-2: #98bde6;
    --row-3: #7eabde;
    --row-4: #6496d2;
    --row-5: #4a84cb;
    --row-6: #3371c2;
    --row-7: #1c5cb8;
    --row-8: #0047ab;
    --art-light: #4d8ad9;
    --art-deep: #0a4bb0;
    --text: #ffffff;
  }
  * { margin: 0; padding: 0; box-sizing: border-box; }
  html, body { width: 704px; height: 1200px; overflow: hidden; background: var(--page); }
  .rules { position: absolute; left: 81px; top: 65px; width: 542px; }
  .rule { position: relative; height: 133.6px; display: flex; }
  .rule--icon-right { flex-direction: row-reverse; }
  .rule__icon {
    position: relative; width: 134px; flex: none; background: var(--panel-light);
    display: flex; align-items: center; justify-content: center;
  }
  .rule__icon::after {
    content: ""; position: absolute; top: 24px; width: 0; height: 0;
    border-top: 11px solid transparent; border-bottom: 11px solid transparent;
  }
  .rule--icon-left .rule__icon::after { right: -13px; border-left: 13px solid var(--panel-light); }
  .rule--icon-right .rule__icon::after { left: -13px; border-right: 13px solid var(--panel-light); }
  .rule__art {
    width: 82px; height: 82px; border-radius: 10px;
    background: linear-gradient(135deg, var(--art-light), var(--art-deep));
  }
  .rule__body { flex: 1; color: var(--text); }
  .rule--icon-left .rule__body { padding: 16px 26px 0 34px; }
  .rule--icon-right .rule__body { padding: 16px 27px 0 26px; }
  .rule__title {
    font-family: "Barlow", sans-serif; font-weight: 400; font-size: 19.5px;
    line-height: 24px; margin-bottom: 8px; letter-spacing: 0.2px;
  }
  .rule__num { display: inline-block; margin-right: 14px; }
  .rule__text {
    font-family: "Montserrat", sans-serif; font-weight: 500; font-size: 8.6px;
    line-height: 10.7px; text-align: justify; hyphens: auto;
  }
  .rule--1 .rule__body { background: var(--row-1); padding-left: 38px; }
  .rule--1 .rule__title { margin-bottom: 12px; }
  .rule--2 .rule__body { background: var(--row-2); }
  .rule--3 .rule__body { background: var(--row-3); padding-top: 24px; padding-left: 23px; padding-right: 14px; }
  .rule--4 .rule__body { background: var(--row-4); }
  .rule--5 .rule__body { background: var(--row-5); padding-top: 24px; }
  .rule--6 .rule__body { background: var(--row-6); padding-top: 27px; }
  .rule--7 .rule__body { background: var(--row-7); padding-top: 23px; }
  .rule--8 .rule__body { background: var(--row-8); padding-top: 26px; }
</style>
</head>
<body>
<main class="rules">
  <section class="rule rule--1 rule--icon-left">
    <div class="rule__icon"><div class="rule__art" role="img" aria-label="Illustration of an envelope with a question mark"></div></div>
    <div class="rule__body">
      <h2 class="rule__title"><span class="rule__num">01</span>A Few Quick Rules</h2>
      <p class="rule__text">We are here to help each step of the way. While questions are never discouraged, this letter will answer some of the most common ones we get asked.</p>
    </div>
  </section>

  <section class="rule rule--2 rule--icon-right">
    <div class="rule__icon"><div class="rule__art" role="img" aria-label="Illustration of a speech bubble"></div></div>
    <div class="rule__body">
      <h2 class="rule__title"><span class="rule__num">02</span>Communications</h2>
      <p class="rule__text">As a client, you should always be in the loop. While we will try to respond to questions as quickly as possible, sometimes we are unable to respond right away. Do not worry - we promise to get back to you soon. Some questions might take some time to research, and a correct answer is better than a quick one.</p>
    </div>
  </section>

  <section class="rule rule--3 rule--icon-left">
    <div class="rule__icon"><div class="rule__art" role="img" aria-label="Illustration of a calendar"></div></div>
    <div class="rule__body">
      <h2 class="rule__title"><span class="rule__num">03</span>Appointments</h2>
      <p class="rule__text">One of the benefits of having an attorney is the ability to discuss your case outside of court, minus the stress and headaches. If you need an appointment, please contact the office.<br>Appointments must be scheduled in advance. We do not want you to make a special trip to the office only to learn that we are in court or otherwise unavailable.</p>
    </div>
  </section>

  <section class="rule rule--4 rule--icon-right">
    <div class="rule__icon"><div class="rule__art" role="img" aria-label="Illustration of jail bars with a lock"></div></div>
    <div class="rule__body">
      <h2 class="rule__title"><span class="rule__num">04</span>Jail Visits</h2>
      <p class="rule__text">If your family member is currently in jail, we take that very seriously. We will visit your loved one and introduce ourselves. While the case is ongoing, we ask that a family member be designated a “contact” person so that messages can be relayed quickly. Never discuss the facts of the case over the phone with someone who is in jail. Jail calls are recorded and we have seen too many cases go south based on remarks made over recorded lines.</p>
    </div>
  </section>

  <section class="rule rule--5 rule--icon-left">
    <div class="rule__icon"><div class="rule__art" role="img" aria-label="Illustration of a police report under a magnifying glass"></div></div>
    <div class="rule__body">
      <h2 class="rule__title"><span class="rule__num">05</span>Police Reports and Discovery</h2>
      <p class="rule__text">We will do our best to provide you with copies of everything we receive on your case. Most information will be emailed, so please keep your email address up to date.</p>
    </div>
  </section>

  <section class="rule rule--6 rule--icon-right">
    <div class="rule__icon"><div class="rule__art" role="img" aria-label="Illustration of a document and a phone book being updated"></div></div>
    <div class="rule__body">
      <h2 class="rule__title"><span class="rule__num">06</span>Changes in Contact Information</h2>
      <p class="rule__text">If you move or change numbers during the case, please let us know. It is difficult to help if we are unable to reach you, and helping you is why we are here.</p>
    </div>
  </section>

  <section class="rule rule--7 rule--icon-left">
    <div class="rule__icon"><div class="rule__art" role="img" aria-label="Illustration of a judge's gavel"></div></div>
    <div class="rule__body">
      <h2 class="rule__title"><span class="rule__num">07</span>Court Appearances</h2>
      <p class="rule__text">Cases do not get resolved as quickly as they do on television. Expect there to be several hearings in your case and it may be necessary for you to attend one or more of them. If a hearing is set, you will receive notice of the date and time of each hearing.</p>
    </div>
  </section>

  <section class="rule rule--8 rule--icon-right">
    <div class="rule__icon"><div class="rule__art" role="img" aria-label="Illustration of a client with a speech bubble and a banknote"></div></div>
    <div class="rule__body">
      <h2 class="rule__title"><span class="rule__num">08</span>Billing and Collections</h2>
      <p class="rule__text">We understand that this investment was a huge decision for you. As we focus on providing the best representation, we will need for you to stay on schedule with any payment arrangements agreed to at the time of your initial consultation.</p>
    </div>
  </section>
</main>
</body>
</html>
```